Single-sided business card for restaurant velmora with new logo made on this site

Business card options with new logo including restaurant name, address, phone number and website. This business card is single-sided only and will be presented at the hostess desk for clients to take. I would like to see options based on a cream card background, a white card background, a yellow card background and a burgundy colored background. It needs to be elegant and traditional.

Target Market(s)

local and international crowd

Industry/Entity Type

restaurant

Contact Information for Business Card

address, website and phone number

Font styles to use
Serif

Colors
EE7325
F08F49
F5BC92
FAE3D3
FDF4ED

Requirements
Must have
• new logo, address, phone number, website
Should not have
• more than three colors

```html
<!DOCTYPE html>
<html lang="es">
<head>
<meta charset="utf-8">
<title>Velmora – Business Card Options</title>
<link rel="stylesheet" href="https://fonts.googleapis.com/css2?family=Cinzel:wght@500;600&family=Cormorant+SC:wght@500&family=Poppins:wght@500;600&display=swap">
<style>
  :root {
    --stage: #dcdcdc;
    --burgundy: #4a1f1c;
    --ink: #3e1a17;
    --gold: #eaaf27;
    --yellow: #eeae2f;
    --cream: #f6f1d4;
    --white: #f1f0ee;
    --paper-white: #fbfaf6;
  }
  * { box-sizing: border-box; margin: 0; padding: 0; }
  html, body { width: 799px; height: 1200px; overflow: hidden; background: var(--stage); }
  .sheet { position: relative; width: 799px; height: 1200px; }

  .card {
    position: absolute;
    width: 281px;
    height: 490px;
    box-shadow: 3px 5px 8px rgba(0,0,0,.28);
    --bg: var(--burgundy);
    --fg: var(--paper-white);
    --line: var(--paper-white);
    --mark: var(--paper-white);
    --icon: var(--gold);
    --rule: var(--paper-white);
    background: var(--bg);
    color: var(--fg);
  }
  .card--burgundy { left: 101px; top: 103px; }
  .card--yellow   { left: 412px; top: 103px; --bg: var(--yellow); --fg: var(--ink); --line: var(--ink); --mark: var(--ink); --icon: var(--ink); --rule: var(--ink); }
  .card--white    { left: 97px;  top: 612px; --bg: var(--white); --fg: var(--ink); --line: var(--gold); --mark: var(--gold); --icon: var(--gold); --rule: var(--gold); }
  .card--cream    { left: 408px; top: 612px; --bg: var(--cream); --fg: var(--ink); --line: var(--ink); --mark: var(--ink); --icon: var(--gold); --rule: var(--gold); }

  .card__frame {
    position: absolute;
    inset: 7px;
    border: 3px solid var(--line);
  }

  .card__content {
    position: absolute;
    inset: 0;
    display: flex;
    flex-direction: column;
    align-items: center;
  }

  .brand__square {
    margin-top: 44px;
    width: 108px;
    height: 108px;
    background: var(--mark);
  }
  .brand__name {
    margin-top: 22px;
    font-family: "Cinzel", serif;
    font-weight: 500;
    font-size: 30px;
    letter-spacing: 4px;
    color: var(--fg);
    line-height: 1;
    padding-left: 4px;
  }
  .brand__since {
    margin-top: 10px;
    display: flex;
    align-items: center;
    gap: 12px;
    font-family: "Cormorant SC", serif;
    font-size: 11px;
    letter-spacing: .5px;
    color: var(--fg);
  }
  .brand__since::before,
  .brand__since::after {
    content: "";
    width: 48px;
    height: 1.5px;
    background: var(--rule);
  }

  .contact { font-family: "Poppins", sans-serif; font-weight: 600; text-align: center; color: var(--fg); }
  .contact__pin { margin-top: 46px; width: 18px; height: 27px; }
  .contact__address { margin-top: 9px; font-size: 13.5px; line-height: 16.5px; letter-spacing: .3px; }
  .contact__icons { margin-top: 38px; display: flex; gap: 5px; }
  .contact__icons svg { width: 15px; height: 15px; }
  .contact__phone { margin-top: 8px; font-size: 12px; letter-spacing: 1px; line-height: 16px; }
  .contact__web { font-size: 12px; letter-spacing: .6px; line-height: 16px; }
</style>
</head>
<body>
<main class="sheet">

  <!-- burgundy -->
  <article class="card card--burgundy">
    <div class="card__frame"></div>
    <div class="card__content">
      <div class="brand__square"></div>
      <div class="brand__name">VELMORA</div>
      <div class="brand__since">Desde 1999</div>
      <div class="contact">
        <svg class="contact__pin" viewBox="0 0 18 27"><path d="M9 1a8 8 0 0 0-8 8c0 6 8 13 8 13s8-7 8-13a8 8 0 0 0-8-8z" fill="var(--icon)"/><circle cx="9" cy="9" r="3" fill="var(--bg)"/><rect x="3" y="24.5" width="12" height="2" fill="var(--icon)"/></svg>
        <p class="contact__address">Almendro 418<br>Colonia Las Palmas,<br>Oaxaca CP 70942</p>
        <div class="contact__icons" style="justify-content:center">
          <svg viewBox="0 0 16 16"><circle cx="8" cy="8" r="8" fill="var(--icon)"/><path d="M5.2 4.2l1.4-.3.9 2-1 .8c.5 1.1 1.3 1.9 2.4 2.4l.8-1 2 .9-.3 1.4c-3.4.2-6.4-2.8-6.2-6.2z" fill="var(--bg)"/></svg>
          <svg viewBox="0 0 16 16"><circle cx="8" cy="8" r="8" fill="var(--icon)"/><g fill="none" stroke="var(--bg)" stroke-width="1"><circle cx="8" cy="8" r="4.8"/><ellipse cx="8" cy="8" rx="2" ry="4.8"/><path d="M3.2 8h9.6M4 5.5h8M4 10.5h8"/></g></svg>
        </div>
        <p class="contact__phone">958-204-3378</p>
        <p class="contact__web">www.velmora.com.mx</p>
      </div>
    </div>
  </article>

  <!-- yellow -->
  <article class="card card--yellow">
    <div class="card__frame"></div>
    <div class="card__content">
      <div class="brand__square"></div>
      <div class="brand__name">VELMORA</div>
      <div class="brand__since">Desde 1999</div>
      <div class="contact">
        <svg class="contact__pin" viewBox="0 0 18 27"><path d="M9 1a8 8 0 0 0-8 8c0 6 8 13 8 13s8-7 8-13a8 8 0 0 0-8-8z" fill="var(--icon)"/><circle cx="9" cy="9" r="3" fill="var(--bg)"/><rect x="3" y="24.5" width="12" height="2" fill="var(--icon)"/></svg>
        <p class="contact__address">Almendro 418<br>Colonia Las Palmas,<br>Oaxaca CP 70942</p>
        <div class="contact__icons" style="justify-content:center">
          <svg viewBox="0 0 16 16"><circle cx="8" cy="8" r="8" fill="var(--icon)"/><path d="M5.2 4.2l1.4-.3.9 2-1 .8c.5 1.1 1.3 1.9 2.4 2.4l.8-1 2 .9-.3 1.4c-3.4.2-6.4-2.8-6.2-6.2z" fill="var(--bg)"/></svg>
          <svg viewBox="0 0 16 16"><circle cx="8" cy="8" r="8" fill="var(--icon)"/><g fill="none" stroke="var(--bg)" stroke-width="1"><circle cx="8" cy="8" r="4.8"/><ellipse cx="8" cy="8" rx="2" ry="4.8"/><path d="M3.2 8h9.6M4 5.5h8M4 10.5h8"/></g></svg>
        </div>
        <p class="contact__phone">958-204-3378</p>
        <p class="contact__web">www.velmora.com.mx</p>
      </div>
    </div>
  </article>

  <!-- white -->
  <article class="card card--white">
    <div class="card__frame"></div>
    <div class="card__content">
      <div class="brand__square"></div>
      <div class="brand__name">VELMORA</div>
      <div class="brand__since">Desde 1999</div>
      <div class="contact">
        <svg class="contact__pin" viewBox="0 0 18 27"><path d="M9 1a8 8 0 0 0-8 8c0 6 8 13 8 13s8-7 8-13a8 8 0 0 0-8-8z" fill="var(--icon)"/><circle cx="9" cy="9" r="3" fill="var(--bg)"/><rect x="3" y="24.5" width="12" height="2" fill="var(--icon)"/></svg>
        <p class="contact__address">Almendro 418<br>Colonia Las Palmas,<br>Oaxaca CP 70942</p>
        <div class="contact__icons" style="justify-content:center">
          <svg viewBox="0 0 16 16"><circle cx="8" cy="8" r="8" fill="var(--icon)"/><path d="M5.2 4.2l1.4-.3.9 2-1 .8c.5 1.1 1.3 1.9 2.4 2.4l.8-1 2 .9-.3 1.4c-3.4.2-6.4-2.8-6.2-6.2z" fill="var(--bg)"/></svg>
          <svg viewBox="0 0 16 16"><circle cx="8" cy="8" r="8" fill="var(--icon)"/><g fill="none" stroke="var(--bg)" stroke-width="1"><circle cx="8" cy="8" r="4.8"/><ellipse cx="8" cy="8" rx="2" ry="4.8"/><path d="M3.2 8h9.6M4 5.5h8M4 10.5h8"/></g></svg>
        </div>
        <p class="contact__phone">958-204-3378</p>
        <p class="contact__web">www.velmora.com.mx</p>
      </div>
    </div>
  </article>

  <!-- cream -->
  <article class="card card--cream">
    <div class="card__frame"></div>
    <div class="card__content">
      <div class="brand__square"></div>
      <div class="brand__name">VELMORA</div>
      <div class="brand__since">Desde 1999</div>
      <div class="contact">
        <svg class="contact__pin" viewBox="0 0 18 27"><path d="M9 1a8 8 0 0 0-8 8c0 6 8 13 8 13s8-7 8-13a8 8 0 0 0-8-8z" fill="var(--icon)"/><circle cx="9" cy="9" r="3" fill="var(--bg)"/><rect x="3" y="24.5" width="12" height="2" fill="var(--icon)"/></svg>
        <p class="contact__address">Almendro 418<br>Colonia Las Palmas,<br>Oaxaca CP 70942</p>
        <div class="contact__icons" style="justify-content:center">
          <svg viewBox="0 0 16 16"><circle cx="8" cy="8" r="8" fill="var(--icon)"/><path d="M5.2 4.2l1.4-.3.9 2-1 .8c.5 1.1 1.3 1.9 2.4 2.4l.8-1 2 .9-.3 1.4c-3.4.2-6.4-2.8-6.2-6.2z" fill="var(--bg)"/></svg>
          <svg viewBox="0 0 16 16"><circle cx="8" cy="8" r="8" fill="var(--icon)"/><g fill="none" stroke="var(--bg)" stroke-width="1"><circle cx="8" cy="8" r="4.8"/><ellipse cx="8" cy="8" rx="2" ry="4.8"/><path d="M3.2 8h9.6M4 5.5h8M4 10.5h8"/></g></svg>
        </div>
        <p class="contact__phone">958-204-3378</p>
        <p class="contact__web">www.velmora.com.mx</p>
      </div>
    </div>
  </article>

</main>
</body>
</html>
```